High end Electrical/home automation Business Card

Need a card for a high end electrical and home automation company utilising the existing logo.
Phone
Email
Website

Like black look with raised detail. Don’t necessarily need to keep colour of logo it could be made grayscale or white etc

Target Market(s)

High end clients

Contact Information for Business Card

Brightmoor Electrical

Requirements
Must have
• Logo, phone, email, website, address

High end look
Nice to have
• Black background card
Raised font
Should not have
• Lots of colour

```html
<!DOCTYPE html>
<html lang="en">
<head>
<meta charset="utf-8">
<title>Brightmoor Electrical – Business Card</title>
<link href="https://fonts.googleapis.com/css2?family=Archivo:wght@400;800&display=swap" rel="stylesheet">
<style>
  :root {
    --backdrop: #161616;
    --card: #202020;
    --white: #ffffff;
    --blue: #2393d3;
    --muted: #e8e8e8;
  }
  * { margin: 0; padding: 0; box-sizing: border-box; }
  html, body {
    width: 1200px; height: 988px; overflow: hidden;
    background: var(--backdrop);
    font-family: "Archivo", Arial, sans-serif;
  }
  .canvas {
    width: 1200px; height: 988px;
    display: flex; flex-direction: column;
    align-items: center; justify-content: center; gap: 56px;
  }
  .card {
    position: relative;
    width: 700px; height: 400px;
    background: var(--card);
    border-radius: 22px;
    overflow: hidden;
  }

  /* Front */
  .card-front { display: flex; flex-direction: column; align-items: center; justify-content: center; gap: 26px; }
  .brand-dot { width: 92px; height: 92px; border-radius: 50%; background: var(--blue); }
  .brand-name { color: var(--white); font-weight: 800; font-size: 44px; letter-spacing: -0.5px; white-space: nowrap; }

  /* Back */
  .card-back .brand-name {
    position: absolute; left: 70px; top: 96px; font-size: 30px;
  }
  .brand-ring {
    position: absolute; right: 50px; top: 40px;
    width: 200px; height: 200px; border-radius: 50%;
    border: 28px solid var(--blue);
  }
  .accent-tab {
    position: absolute; left: 0; top: 172px;
    width: 42px; height: 40px; background: var(--blue);
  }
  .person { position: absolute; left: 70px; top: 166px; }
  .person-name { color: var(--blue); font-weight: 800; font-size: 30px; line-height: 1; white-space: nowrap; }
  .person-role { color: var(--muted); font-size: 17px; margin-top: 3px; }
  .address { position: absolute; left: 70px; top: 240px; color: var(--muted); font-size: 17px; line-height: 1.3; font-style: normal; }
  .contacts { position: absolute; left: 70px; top: 294px; list-style: none; }
  .contacts li { display: flex; align-items: center; gap: 10px; color: var(--muted); font-size: 17px; line-height: 1.5; white-space: nowrap; }
  .contacts svg { width: 16px; height: 16px; fill: var(--blue); flex: none; }
  .highlight { color: var(--blue); }
</style>
</head>
<body>
<main class="canvas">
  <section class="card card-front">
    <div class="brand-dot"></div>
    <div class="brand-name">Brightmoor Electrical</div>
  </section>

  <section class="card card-back">
    <div class="brand-name">Brightmoor Electrical</div>
    <div class="brand-ring"></div>
    <div class="accent-tab"></div>
    <div class="person">
      <div class="person-name">Daniel Marsh</div>
      <div class="person-role">Co-Founder</div>
    </div>
    <address class="address">
      4820 Harwell Park Rd<br>Suite C Dayton.
    </address>
    <ul class="contacts">
      <li>
        <svg viewBox="0 0 16 16" aria-hidden="true"><path d="M3.5 1l2.5 3-1.5 2a8 8 0 0 0 5 5l2-1.5 3 2.5-1.5 2.5C7 15 1 9 1 2.5z"/></svg>
        123-555-0148
      </li>
      <li>
        <svg viewBox="0 0 16 16" aria-hidden="true"><path d="M1 3h14v10H1z M1 3l7 6 7-6" fill="none" stroke="#2393d3" stroke-width="1.6"/></svg>
        daniel@brightmoorelectrical.com
      </li>
      <li>
        <svg viewBox="0 0 16 16" aria-hidden="true"><circle cx="8" cy="8" r="7"/></svg>
        <span>www.<span class="highlight">brightmoorelectrical</span>.com</span>
      </li>
    </ul>
  </section>
</main>
</body>
</html>
```